Harborline Auto LLC

Car Dealer Customer Service
Address: 2874 Cresthaven Road, Shelbyville, TN 37162
web: www.harborlineautoxq.net
email: harborlineautoxq@mailnest.example
Phone: (931) 555-0148
Phone: (629) 555-0173

```html
<!DOCTYPE html>
<html lang="en">
<head>
<meta charset="utf-8">
<title>Harborline Auto – Business Card</title>
<link rel="stylesheet" href="https://fonts.googleapis.com/css2?family=Montserrat:wght@400;500;800&display=swap">
<style>
  :root {
    --brand-blue: #1c7db0;
    --accent-blue: #2791cf;
    --brand-gold: #ecb13f;
    --ink: #1a1a1a;
    --paper: #ffffff;
    --backdrop: #cfcfcf;
  }
  * { box-sizing: border-box; margin: 0; padding: 0; }
  html, body {
    width: 1200px; height: 813px; overflow: hidden;
    background: var(--backdrop);
    font-family: "Montserrat", sans-serif;
  }
  .sheet {
    position: relative; width: 1200px; height: 813px;
    display: flex; align-items: center; justify-content: center; gap: 40px;
  }
  .card {
    position: relative; width: 525px; height: 300px;
    border-radius: 22px; overflow: hidden;
    box-shadow: 0 8px 22px rgba(0,0,0,.25);
  }

  /* Front */
  .card--front { background: var(--paper); }
  .front__accent {
    position: absolute; top: 28px; right: 0;
    width: 30px; height: 14px; background: var(--accent-blue);
  }
  .front__address {
    position: absolute; top: 26px; right: 42px;
    text-align: right; font-size: 13.5px; line-height: 1.35;
    color: var(--ink); font-weight: 500;
  }
  .front__brand {
    position: absolute; left: 34px; top: 150px;
    display: flex; align-items: center; gap: 12px;
  }
  .brand__dot {
    width: 46px; height: 46px; border-radius: 50%;
    background: var(--brand-gold);
  }
  .front__name {
    font-size: 24px; font-weight: 800; letter-spacing: .02em;
    color: var(--brand-blue); text-transform: uppercase;
  }
  .front__contacts {
    position: absolute; left: 40px; top: 210px;
    list-style: none; font-size: 12.5px; line-height: 1.45;
    color: var(--ink); font-weight: 500;
  }
  .front__contacts li { display: flex; align-items: center; gap: 10px; }
  .contact__icon { width: 12px; height: 12px; flex: none; fill: var(--accent-blue); }

  /* Back */
  .card--back {
    background: var(--brand-blue);
    border-bottom: 5px solid var(--brand-gold);
    display: flex; flex-direction: column; align-items: center; justify-content: center; gap: 22px;
  }
  .back__dot {
    width: 120px; height: 120px; border-radius: 50%;
    background: var(--brand-gold);
  }
  .back__name {
    font-size: 36px; font-weight: 800; letter-spacing: .03em;
    color: var(--paper); text-transform: uppercase;
  }
</style>
</head>
<body>
<main class="sheet">
  <section class="card card--front">
    <div class="front__accent"></div>
    <p class="front__address">Car Dealer Customer Service<br>2874 Cresthaven Road<br>Shelbyville, TN 37162</p>

    <div class="front__brand">
      <span class="brand__dot"></span>
      <span class="front__name">Harborline Auto</span>
    </div>

    <ul class="front__contacts">
      <li>
        <svg class="contact__icon" viewBox="0 0 24 24" aria-hidden="true"><path d="M6.6 10.8a15 15 0 0 0 6.6 6.6l2.2-2.2c.3-.3.7-.4 1-.2 1.1.4 2.3.6 3.6.6.6 0 1 .4 1 1V20c0 .6-.4 1-1 1A17 17 0 0 1 3 4c0-.6.4-1 1-1h3.5c.6 0 1 .4 1 1 0 1.3.2 2.5.6 3.6.1.3 0 .7-.2 1z"/></svg>
        (931) 555-0148
      </li>
      <li>
        <svg class="contact__icon" viewBox="0 0 24 24" aria-hidden="true"><path d="M6.6 10.8a15 15 0 0 0 6.6 6.6l2.2-2.2c.3-.3.7-.4 1-.2 1.1.4 2.3.6 3.6.6.6 0 1 .4 1 1V20c0 .6-.4 1-1 1A17 17 0 0 1 3 4c0-.6.4-1 1-1h3.5c.6 0 1 .4 1 1 0 1.3.2 2.5.6 3.6.1.3 0 .7-.2 1z"/></svg>
        (629) 555-0173
      </li>
      <li>
        <svg class="contact__icon" viewBox="0 0 24 24" aria-hidden="true"><path d="M2 5h20v14H2z M2 5l10 8 10-8" fill="none" stroke="#2791cf" stroke-width="2.4"/></svg>
        harborlineautoxq@mailnest.example
      </li>
      <li>
        <svg class="contact__icon" viewBox="0 0 24 24" aria-hidden="true"><circle cx="12" cy="12" r="10" fill="none" stroke="#2791cf" stroke-width="2.4"/><path d="M2 12h20M12 2c3 3 3 17 0 20M12 2c-3 3-3 17 0 20" fill="none" stroke="#2791cf" stroke-width="2"/></svg>
        www.harborlineautoxq.net
      </li>
    </ul>
  </section>

  <section class="card card--back">
    <span class="back__dot"></span>
    <span class="back__name">Harborline Auto</span>
  </section>
</main>
</body>
</html>
```